Summit Builders Web Site / Business Cards

Construction Company that specializes in Water and Fire Damage, Residential ReModels, Landscaping and Building ADU (Accessory Dwelling Unit)

Growing and changing families often need additional space, and a remodeling project can often provide that. Adding a new area, or repurposing an existing one can satisfy this requirement.

Other times, homeowners want to update the look in their kitchen or bathroom with more than just a change of cabinetry or vanity doors and drawers. Whatever your needs are, Summit Builders has skilled workers who are bonded and insured, and ready to make your dreams and visions a reality.

Target Market(s)

Home Owners

Industry/Entity Type

Construction Company

Contact Information for Business Card

Center Logo with our information on the corners

Back side to be Logo Only
Contact Info
CSLB License # 2418596
info@summitbuildersca.example
www.summitbuildersca.example

Coding

Coded - Design and coding required

Number of Pages Required

5+ page

Font styles to use
Serif
Sans Serif

Requirements
Must have
• Using our Logo Colors
Home
About Us
Services
Projects / Portfolio
Contact Us
Nice to have
• Colors matching our Logo
Should not have
• Black because it doesnt match our logo

```html
<!DOCTYPE html>
<html lang="en">
<head>
<meta charset="utf-8">
<title>Summit Builders — Landscaping &amp; Building ADU</title>
<link rel="stylesheet" href="https://fonts.googleapis.com/css2?family=Open+Sans:wght@400;600;700&family=Ubuntu:wght@400;500;700&display=swap">
<style>
:root{
  --orange:#ff6a00;
  --orange-deep:#f05a00;
  --ink:#222;
  --text:#555;
  --muted:#8a8a8a;
  --soft:#f5f5f5;
  --line:#e4e4e4;
  --white:#fff;
  --bar:#242424;
}
*{box-sizing:border-box;margin:0;padding:0}
html,body{width:1200px;height:3977px;overflow:hidden}
body{font-family:"Open Sans",sans-serif;color:var(--text);background:var(--white);font-size:13px}
section,header,footer{position:relative;width:1200px;overflow:hidden}
.abs{position:absolute}
h1,h2,h3,h4,.num,.brand{font-family:"Ubuntu",sans-serif}
a{color:inherit;text-decoration:none}

/* top bar + header */
.topbar{height:28px;background:var(--white)}
.topbar .grey{position:absolute;left:664px;top:0;width:536px;height:28px;background:#f2f2f2;clip-path:polygon(14px 0,100% 0,100% 100%,0 100%)}
.topbar .iso{position:absolute;left:664px;top:0;width:140px;height:28px;background:#e8e8e8;clip-path:polygon(14px 0,100% 0,126px 100%,0 100%);color:var(--orange);font-size:11px;line-height:28px;padding-left:32px}
.topbar .mail{position:absolute;left:823px;top:0;line-height:28px;font-size:11px;color:#666}
.topbar .social{position:absolute;left:1022px;top:8px;display:flex;gap:14px}
.dot{width:11px;height:11px;border-radius:50%;background:#777}
.navbar{height:68px;border-bottom:1px solid var(--line)}
.brand{position:absolute;left:88px;top:-16px;display:flex;align-items:center;gap:8px;font-weight:700;font-size:24px;letter-spacing:1px;color:var(--ink);height:60px;background:var(--white);padding:0 4px}
.brand .mark{width:14px;height:14px;background:var(--orange)}
.nav{position:absolute;left:372px;top:0;height:68px;display:flex;align-items:center;gap:0;font-size:13px;color:var(--ink)}
.nav a{margin-right:34px}
.nav a.active{color:var(--orange)}
.phone{position:absolute;left:818px;top:0;height:68px;display:flex;align-items:center;gap:8px;font-weight:600;font-size:13px;color:var(--ink)}
.quote{position:absolute;left:968px;top:20px;width:144px;height:30px;border:1px solid var(--orange);color:var(--orange);font-size:11px;text-align:center;line-height:28px;letter-spacing:.3px}

/* hero */
.hero{height:552px}
.hero .photo{position:absolute;inset:0;background:linear-gradient(180deg,#5d6270 0%,#7b7e86 35%,#8e8066 65%,#5a4b3a 100%)}
.hero .shade{position:absolute;inset:0;background:rgba(30,30,40,.28)}
.hero h1{position:absolute;top:270px;width:100%;text-align:center;color:var(--white);font-size:42px;font-weight:500;letter-spacing:1px}
.hero p{position:absolute;left:322px;top:340px;width:556px;text-align:center;color:#f2f2f2;font-size:14px;line-height:23px}
.btn-solid{position:absolute;left:528px;top:346px;width:144px;height:36px;background:var(--orange);color:var(--white);font-size:11px;font-weight:700;text-align:center;line-height:36px}
.arrow{position:absolute;top:260px;width:34px;height:34px;border-radius:50%;background:rgba(255,255,255,.35);display:flex;align-items:center;justify-content:center}

/* section headings */
.kicker{position:absolute;width:100%;text-align:center;color:var(--orange);font-size:13px}
.title{position:absolute;width:100%;text-align:center;color:var(--ink);font-size:34px;font-weight:500;line-height:40px}

/* services */
.services{height:592px;background:var(--soft)}
.cards{position:absolute;left:88px;top:186px;width:1024px;height:295px;display:flex;gap:2px}
.card{flex:1;background:var(--white);text-align:center;padding-top:38px}
.card.lift{box-shadow:0 6px 18px rgba(0,0,0,.08)}
.card h3{font-size:17px;font-weight:500;color:var(--ink);margin:22px 0 12px}
.card p{font-size:11.5px;line-height:21px;color:var(--muted);padding:0 40px}
.go{width:36px;height:36px;border-radius:50%;margin:26px auto 0;display:flex;align-items:center;justify-content:center;border:1px solid var(--line)}
.go.on{background:var(--orange);border-color:var(--orange)}
.btn-line{position:absolute;height:31px;border:2px solid #999;font-size:10px;font-weight:600;color:var(--ink);text-align:center;line-height:27px;letter-spacing:.3px;background:var(--white)}

/* about */
.about{height:563px}
.about .back{position:absolute;left:180px;top:100px;width:368px;height:400px;background:#f3f3f3}
.about .photo{position:absolute;left:156px;top:75px;width:367px;height:399px;background:linear-gradient(160deg,#6e8fbe 0%,#9cb1cf 30%,#a58a68 60%,#7a5e40 100%)}
.about .kick{position:absolute;left:602px;top:100px;color:var(--orange);font-size:13px}
.about h2{position:absolute;left:602px;top:125px;font-size:34px;font-weight:500;color:var(--ink)}
.about p{position:absolute;left:602px;top:184px;width:390px;font-size:11.5px;line-height:21px;color:var(--muted)}
.ticks{position:absolute;left:602px;top:266px;list-style:none}
.ticks li{display:flex;align-items:center;gap:12px;height:33px;font-size:13px;color:var(--ink);letter-spacing:.4px}

/* stats */
.stats{height:141px;background:linear-gradient(90deg,#ff6f0a,#ff7a1c 50%,#ff6a00)}
.stat{position:absolute;top:0;width:222px;height:141px;text-align:center;color:var(--white)}
.stat .num{font-size:40px;font-weight:500;margin-top:32px}
.stat .lbl{font-size:15px;margin-top:2px;color:#ffe7d6}
.sep{position:absolute;top:0;width:1px;height:141px;background:rgba(255,255,255,.22)}

/* projects */
.projects{height:784px}
.tile{position:absolute}
.tile.over::after{content:"";position:absolute;inset:0;background:rgba(255,106,0,.82)}
.plus{position:absolute;z-index:1;left:98px;top:82px}

/* testimonial */
.quote-band{height:369px;background:var(--orange);color:var(--white)}
.quote-band .q{position:absolute;left:0;width:100%;top:56px;text-align:center;font-family:"Ubuntu",sans-serif;font-size:60px;line-height:60px;font-weight:500}
.quote-band p{position:absolute;left:320px;top:110px;width:560px;text-align:center;font-size:17px;line-height:32px}
.avatar{position:absolute;left:570px;top:228px;width:60px;height:60px;border-radius:50%;background:radial-gradient(circle at 50% 40%,#d7b49a,#8b6a55);border:3px solid #ffb57f}
.quote-band .who{position:absolute;top:300px;width:100%;text-align:center;font-size:14px;color:#ffe3cf}
.pager{position:absolute;left:1075px;top:190px;display:flex;flex-direction:column;gap:5px}
.pager span{width:8px;height:8px;border-radius:50%;border:1px solid #ffd1b0}

/* blog */
.blog{height:439px}
.post{position:absolute;top:139px;width:284px;height:240px}
.post .date{position:absolute;left:17px;top:14px;width:43px;height:42px;background:var(--white);text-align:center;color:var(--orange);font-family:"Ubuntu",sans-serif;font-size:18px;font-weight:700;line-height:20px;padding-top:4px}
.post .date small{display:block;font-size:8px;color:var(--muted);font-weight:400;line-height:10px}
.post .cap{position:absolute;left:0;bottom:18px;width:100%;text-align:center;color:var(--white);font-size:11.5px;line-height:19px;padding:0 20px}
.post .veil{position:absolute;inset:0;background:linear-gradient(180deg,rgba(0,0,0,0) 45%,rgba(0,0,0,.5))}

/* footer */
.footer{height:397px}
.footer .rule{position:absolute;left:0;top:43px;width:1200px;height:2px;background:var(--ink)}
.footer .fbrand{position:absolute;left:530px;top:6px;width:140px;height:76px;background:var(--white);display:flex;align-items:center;justify-content:center;gap:8px;font-family:"Ubuntu",sans-serif;font-weight:700;font-size:24px;color:var(--ink);letter-spacing:1px}
.footer .fbrand .mark{width:14px;height:14px;background:var(--orange)}
.col{position:absolute;top:130px;font-size:11.5px;color:var(--ink)}
.col h4{font-size:14px;font-weight:500;display:flex;align-items:center;gap:8px;margin-bottom:18px;margin-left:0}
.col .body{padding-left:22px;line-height:19px}
.col .lab{color:var(--muted);margin-top:10px}
.col a.mail{color:var(--orange);text-decoration:underline}
.links a{display:block;line-height:24px}
.hours p{color:var(--muted);line-height:17px;margin-bottom:14px}
.hours b{font-weight:700;color:var(--ink)}
.hours .row{line-height:23px;color:var(--muted)}
.bottom{position:absolute;left:0;top:3933px;width:1200px;height:44px;background:var(--bar);color:#ddd;font-size:11px}
.bottom .copy{position:absolute;left:88px;top:0;line-height:44px}
.bottom .soc{position:absolute;left:952px;top:7px;display:flex;gap:10px}
.bottom .soc span{width:32px;height:32px;border-radius:50%;border:1px solid #aaa}
.bottom .soc span.on{background:var(--orange);border-color:var(--orange)}
</style>
</head>
<body>

<header class="site-header">
  <div class="topbar">
    <div class="grey"></div>
    <div class="iso">ISO 9001:2017</div>
    <div class="mail">e: hello@summitbuildersca.example</div>
    <div class="social"><span class="dot"></span><span class="dot"></span><span class="dot"></span><span class="dot"></span></div>
  </div>
  <div class="navbar">
    <div class="brand"><span class="mark"></span>SUMMIT</div>
    <nav class="nav">
      <a class="active" href="#">Home</a>
      <a href="#">Services</a>
      <a href="#">About Us</a>
      <a href="#">Our Projects</a>
      <a href="#">Contact Us</a>
    </nav>
    <div class="phone">
      <svg width="13" height="13" viewBox="0 0 24 24"><path d="M6.6 10.8a15 15 0 0 0 6.6 6.6l2.2-2.2a1 1 0 0 1 1-.25 11.4 11.4 0 0 0 3.6.57 1 1 0 0 1 1 1V20a1 1 0 0 1-1 1A17 17 0 0 1 3 4a1 1 0 0 1 1-1h3.5a1 1 0 0 1 1 1c0 1.25.2 2.45.57 3.57a1 1 0 0 1-.25 1z" fill="#ff6a00"/></svg>
      +1 555 014 2290
    </div>
    <a class="quote" href="#">REQUEST A QUOTE</a>
  </div>
</header>

<section class="hero">
  <div class="photo" role="img" aria-label="Construction site with tower cranes and buildings under a cloudy sky"></div>
  <div class="shade"></div>
  <div class="arrow" style="left:16px"><svg width="12" height="12" viewBox="0 0 12 12"><path d="M8 2L4 6l4 4" stroke="#fff" stroke-width="1.5" fill="none"/></svg></div>
  <div class="arrow" style="left:1150px"><svg width="12" height="12" viewBox="0 0 12 12"><path d="M4 2l4 4-4 4" stroke="#fff" stroke-width="1.5" fill="none"/></svg></div>
  <h1 style="top:174px">LANDSCAPING &amp; BUILDING ADU</h1>
  <p style="top:243px">Lorem ipsum is simply dummy text of the printing and typesetting industry. Lorem ipsum has been the industry's standard dummy text, when an unknown printer took a galley of type and scrambled.</p>
  <a class="btn-solid" href="#">CONTACT US</a>
</section>

<section class="services">
  <div class="kicker" style="top:52px">What We do</div>
  <h2 class="title" style="top:72px">Delivering the Best Nationwide<br>Summit Builders</h2>
  <div class="cards">
    <div class="card lift">
      <svg width="40" height="50" viewBox="0 0 40 50"><rect x="12" y="14" width="16" height="32" rx="3" fill="none" stroke="#ff6a00" stroke-width="2.5"/><rect x="16" y="6" width="8" height="8" fill="none" stroke="#ff6a00" stroke-width="2.5"/><path d="M24 9h8l4 6" stroke="#ff6a00" stroke-width="2.5" fill="none"/><rect x="16" y="24" width="8" height="12" fill="#ff6a00"/></svg>
      <h3>Water &amp; Fire Damage Solution</h3>
      <p>Lorem is simply dummy text of the printing and typesetting industry. lorem ipsum has been standard dummy text</p>
      <div class="go on"><svg width="12" height="12" viewBox="0 0 12 12"><path d="M1 6h9M7 3l3 3-3 3" stroke="#fff" stroke-width="1.4" fill="none"/></svg></div>
    </div>
    <div class="card">
      <svg width="54" height="50" viewBox="0 0 54 50"><rect x="4" y="6" width="26" height="42" fill="none" stroke="#777" stroke-width="2.5"/><rect x="30" y="20" width="20" height="28" fill="none" stroke="#777" stroke-width="2.5"/><g fill="#777"><rect x="10" y="13" width="5" height="5"/><rect x="19" y="13" width="5" height="5"/><rect x="10" y="23" width="5" height="5"/><rect x="19" y="23" width="5" height="5"/><rect x="10" y="33" width="5" height="5"/><rect x="19" y="33" width="5" height="5"/><rect x="36" y="27" width="4" height="4"/><rect x="43" y="27" width="4" height="4"/><rect x="36" y="36" width="4" height="4"/><rect x="43" y="36" width="4" height="4"/></g></svg>
      <h3>Residential ReModels</h3>
      <p>Lorem is simply dummy text of the printing and typesetting industry. lorem ipsum has been standard dummy text</p>
      <div class="go"><svg width="12" height="12" viewBox="0 0 12 12"><path d="M1 6h9M7 3l3 3-3 3" stroke="#ff6a00" stroke-width="1.4" fill="none"/></svg></div>
    </div>
    <div class="card">
      <svg width="50" height="50" viewBox="0 0 50 50"><path d="M5 26a20 20 0 0 1 40 0" fill="none" stroke="#777" stroke-width="2.5"/><g fill="#777"><rect x="8" y="26" width="4" height="20"/><rect x="15" y="20" width="4" height="26"/><rect x="23" y="16" width="4" height="30"/><rect x="31" y="20" width="4" height="26"/><rect x="38" y="26" width="4" height="20"/></g></svg>
      <h3>Landscaping and Building ADU</h3>
      <p>Lorem is simply dummy text of the printing and typesetting industry. lorem ipsum has been standard dummy text</p>
      <div class="go"><svg width="12" height="12" viewBox="0 0 12 12"><path d="M1 6h9M7 3l3 3-3 3" stroke="#ff6a00" stroke-width="1.4" fill="none"/></svg></div>
    </div>
  </div>
  <a class="btn-line" href="#" style="left:520px;top:522px;width:159px">EXPLORE MORE &nbsp;»</a>
</section>

<section class="about">
  <div class="back"></div>
  <div class="photo" role="img" aria-label="Construction worker in a hard hat cutting a board with a circular saw"></div>
  <div class="kick">About Us</div>
  <h2>Who We are</h2>
  <p>Lorem ipsum is simply dummy text of the printing and typesetting industry. Lorem ipsum has been the industry's standard dummy text ever since the 1500s, when an unknown printer.</p>
  <ul class="ticks">
    <li><svg width="14" height="14" viewBox="0 0 24 24"><path d="M12 2l3 7 7 .6-5.3 4.7 1.6 7.2L12 17.8 5.7 21.5l1.6-7.2L2 9.6 9 9z" fill="#ff6a00"/></svg>WE'VE REPUTION FOR EXCELLENCE</li>
    <li><svg width="14" height="14" viewBox="0 0 24 24"><rect x="3" y="10" width="4" height="11" fill="none" stroke="#ff6a00" stroke-width="2"/><path d="M7 11l4-8c2 0 3 1 2.5 3L13 10h6a2 2 0 0 1 2 2.3l-1.4 7A2 2 0 0 1 17.6 21H7" fill="none" stroke="#ff6a00" stroke-width="2"/></svg>GUIDED BY COMMITMENT</li>
    <li><svg width="14" height="14" viewBox="0 0 24 24"><path d="M2 9l5-3 5 3 5-3 5 3-10 9z" fill="none" stroke="#ff6a00" stroke-width="2"/></svg>WE BUILD PARTNERSHIPS</li>
    <li><svg width="14" height="14" viewBox="0 0 24 24"><circle cx="8" cy="8" r="3.5" fill="none" stroke="#ff6a00" stroke-width="2"/><circle cx="17" cy="9" r="3" fill="none" stroke="#ff6a00" stroke-width="2"/><path d="M2 21a6 6 0 0 1 12 0M13 20a5 5 0 0 1 9 0" fill="none" stroke="#ff6a00" stroke-width="2"/></svg>A TEAM OF PROFESSIONALS</li>
  </ul>
  <a class="btn-line" href="#" style="left:602px;top:417px;width:128px">LEARN MORE &nbsp;»</a>
</section>

<section class="stats">
  <div class="stat" style="left:156px"><div class="num">53</div><div class="lbl">Total Projects</div></div>
  <div class="sep" style="left:377px"></div>
  <div class="stat" style="left:377px"><div class="num">371</div><div class="lbl">Staff Members</div></div>
  <div class="sep" style="left:599px"></div>
  <div class="stat" style="left:599px"><div class="num">15</div><div class="lbl">Working in States</div></div>
  <div class="sep" style="left:821px"></div>
  <div class="stat" style="left:821px"><div class="num">2,600</div><div class="lbl">Hours for Work</div></div>
</section>

<section class="projects">
  <div class="kicker" style="top:50px">Projects</div>
  <h2 class="title" style="top:70px">Projects Gallery</h2>
  <div class="tile" style="left:88px;top:153px;width:496px;height:279px;background:linear-gradient(170deg,#9fbbe0 0%,#c9d3dd 40%,#c9c0b0 70%,#7b7566 100%)" role="img" aria-label="Modern high school building with a glass entrance"></div>
  <div class="tile" style="left:616px;top:153px;width:232px;height:199px;background:linear-gradient(180deg,#7d8fc0 0%,#8d8aa0 50%,#4d4e55 100%)" role="img" aria-label="Two-storey suburban house at dusk"></div>
  <div class="tile" style="left:879px;top:153px;width:233px;height:199px;background:linear-gradient(180deg,#3f67b8 0%,#8e95a6 50%,#4f6a3a 100%)" role="img" aria-label="Brick family home with front lawn"></div>
  <div class="tile" style="left:88px;top:465px;width:233px;height:200px;background:linear-gradient(180deg,#7bbbe8 0%,#c7b460 45%,#3d8f2e 75%,#2a8fbf 100%)" role="img" aria-label="Large villa surrounded by gardens and a stream"></div>
  <div class="tile over" style="left:352px;top:465px;width:232px;height:200px;background:linear-gradient(180deg,#d9d2c4,#a89c88)" role="img" aria-label="High school building facade"><svg class="plus" width="36" height="36" viewBox="0 0 36 36"><path d="M18 0v36M0 18h36" stroke="#fff" stroke-width="1.5"/></svg></div>
  <div class="tile" style="left:616px;top:384px;width:496px;height:281px;background:linear-gradient(100deg,#e8e4de 0%,#e7c53a 30%,#c99f6a 60%,#8a6a4a 100%)" role="img" aria-label="Worker holding a yellow hard hat beside a tool belt"></div>
  <a class="btn-line" href="#" style="left:528px;top:705px;width:144px">VIEW ALL WORK</a>
</section>

<section class="quote-band">
  <div class="q">“</div>
  <p>Lorem ipsum dolor sit amet, consectetur adipiscing elit, sed do eiusmod tempor incididunt ut labore et dolore magna aliqua. Ut enim ad minim veniam, exercitation ullamco laboris nisi ...</p>
  <div class="avatar" role="img" aria-label="Portrait of the client giving the testimonial"></div>
  <div class="who">Daniel Whitcomb</div>
  <div class="pager"><span style="background:#ffd1b0"></span><span></span><span></span><span></span><span></span></div>
</section>

<section class="blog">
  <div class="kicker" style="top:53px">Our Blogs</div>
  <h2 class="title" style="top:78px">Latest News</h2>
  <article class="post" style="left:156px;background:linear-gradient(160deg,#6e8fbe,#a58a68 60%,#7a5e40)" role="img" aria-label="Construction worker cutting wood">
    <div class="veil"></div><div class="date">10<small>DEC</small></div>
    <div class="cap">LOREM IPSUM IS SIMPLY DUMMY TEXT OF THE PRINTING AND TYPESETTING...</div>
  </article>
  <article class="post" style="left:459px;background:linear-gradient(180deg,#5d6270,#8e8066 70%,#5a4b3a)" role="img" aria-label="Tower cranes over a construction site">
    <div class="veil"></div><div class="date">05<small>DEC</small></div>
    <div class="cap">LOREM IPSUM IS SIMPLY DUMMY TEXT OF THE PRINTING AND TYPESETTING...</div>
  </article>
  <article class="post" style="left:760px;background:linear-gradient(110deg,#e7c53a 0%,#c99f6a 55%,#7a5e40)" role="img" aria-label="Hand holding a yellow hard hat">
    <div class="veil"></div><div class="date">24<small>NOV</small></div>
    <div class="cap">LOREM IPSUM IS SIMPLY DUMMY TEXT OF THE PRINTING AND TYPESETTING...</div>
  </article>
</section>

<footer class="footer">
  <div class="rule"></div>
  <div class="fbrand"><span class="mark"></span>SUMMIT</div>
  <div class="col" style="left:134px">
    <h4><svg width="14" height="12" viewBox="0 0 14 12"><rect x="1" y="1" width="12" height="10" fill="none" stroke="#ff6a00" stroke-width="1.3"/><path d="M3 4h8M3 7h5" stroke="#ff6a00"/></svg>Contact Us</h4>
    <div class="body">
      <div>e. <a class="mail" href="#">hello@summitbuildersca.example</a></div>
      <div class="lab">Phone Number:</div>
      <div>Office: 555-014-2290</div>
      <div>Direct : 555-014-2291</div>
      <div>Fax : 555-014-2292</div>
      <div class="lab">Location:</div>
      <div>418 Harbor Crest Ave Lakeview,<br>CA 90000</div>
    </div>
  </div>
  <div class="col links" style="left:525px">
    <h4><svg width="13" height="13" viewBox="0 0 24 24"><path d="M10 14a5 5 0 0 0 7 0l3-3a5 5 0 0 0-7-7l-1 1M14 10a5 5 0 0 0-7 0l-3 3a5 5 0 0 0 7 7l1-1" fill="none" stroke="#ff6a00" stroke-width="2.2"/></svg>Quick Links</h4>
    <div class="body"><a href="#">Home</a><a href="#">About Us</a><a href="#">Services</a><a href="#">Our Projects</a><a href="#">Contact Us</a></div>
  </div>
  <div class="col hours" style="left:761px;width:300px">
    <h4><svg width="13" height="13" viewBox="0 0 24 24"><circle cx="12" cy="12" r="10" fill="none" stroke="#ff6a00" stroke-width="2.2"/><path d="M12 6v6l4 2" fill="none" stroke="#ff6a00" stroke-width="2.2"/></svg>Working Hours</h4>
    <div class="body">
      <p>we work 7 days a week, every day excluding major holidays. contact us if you have an emergency, with our hotline and contact form.</p>
      <div class="row">monday – friday : <b>10:00 – 16:00</b></div>
      <div class="row">saturday : <b>12:00 – 15:00</b></div>
      <div class="row">sunday and holidays : <b>09:00 – 12:00</b></div>
    </div>
  </div>
</footer>
<div class="bottom">
  <div class="copy">© 2020 Summit Builders - All rights reserved.</div>
  <div class="soc"><span></span><span class="on"></span><span></span><span></span></div>
</div>

</body>
</html>
```